Post storm repair flyer

looking for an eye catching 6x9 postcard to send out to single family home owners advertising a "Post Storm Repair Special" explaining that after the recent hurricanes its very important to have your roof checked and any repairs fixed right away before they become a bigger more costly problem and that even though your home wasn't directly hit by the storm the high wind gust could've cause unseen damage.
offer $200 off any repair *some rules may apply
Crest Roofing
877.512.DUNE
www.DuneRoofingco.example

```html
<!DOCTYPE html>
<html lang="en">
<head>
<meta charset="utf-8">
<title>Crest Roofing – Post Storm Repair Special Postcard</title>
<link rel="stylesheet" href="https://fonts.googleapis.com/css2?family=Rubik+Dirt&family=Poppins:wght@400;500;600;700;800&family=Allura&family=Oswald:wght@600&family=Montserrat:wght@500;600;700;800&display=swap">
<style>
  :root {
    --ink: #0b0b0b;
    --charcoal: #2a2a2c;
    --gold: #e9ae21;
    --white: #ffffff;
    --page: #e6e6e6;
  }
  * { box-sizing: border-box; margin: 0; padding: 0; }
  html, body { width: 922px; height: 1200px; overflow: hidden; }
  body { background: var(--page); position: relative; font-family: "Poppins", sans-serif; }

  .postcard { position: absolute; left: 112px; width: 698px; height: 465px; overflow: hidden; background: var(--white); }
  .postcard--front { top: 95px; }
  .postcard--back { top: 626px; }
  .abs { position: absolute; }

  /* FRONT */
  .front-hero { left: 0; top: 0; width: 698px; height: 254px; background: var(--ink); }
  .storm-photo {
    left: 184px; top: 0; width: 514px; height: 254px;
    background:
      linear-gradient(90deg, var(--ink) 0%, rgba(11,11,11,0) 30%),
      radial-gradient(ellipse at 62% 62%, #e07f1f 0%, #b9601a 18%, #3a3a3c 42%, #1c1c1e 75%);
  }
  .headline-top { left: 43px; top: 30px; font-family: "Rubik Dirt", sans-serif; font-size: 40px; color: var(--white); letter-spacing: 0.5px; line-height: 1; }
  .headline-main { left: 41px; top: 68px; font-family: "Rubik Dirt", sans-serif; font-size: 72px; color: var(--gold); line-height: 1; }
  .headline-script { left: 150px; top: 118px; font-family: "Allura", cursive; font-size: 78px; color: var(--white); line-height: 1; transform: rotate(-6deg); }

  .hex { clip-path: polygon(50% 0, 100% 25%, 100% 75%, 50% 100%, 0 75%, 0 25%); display: flex; align-items: center; justify-content: center; text-align: center; }
  .hex--intro { left: 44px; top: 174px; width: 143px; height: 165px; background: var(--gold); color: var(--white); font-weight: 700; font-size: 14.5px; line-height: 16.5px; padding: 0 8px; }
  .hex--detail-ring { left: 155px; top: 247px; width: 190px; height: 218px; background: var(--white); }
  .hex--detail { left: 157px; top: 250px; width: 186px; height: 212px; background: var(--charcoal); color: var(--white); font-size: 12.3px; line-height: 14.4px; padding: 0 16px; }

  .brand-mark { left: 80px; top: 393px; width: 14px; height: 14px; background: var(--ink); }
  .brand-name { left: 20px; top: 414px; width: 150px; text-align: center; font-weight: 500; font-size: 11.5px; color: var(--ink); letter-spacing: 0.3px; }

  .offer-script { font-family: "Allura", cursive; color: var(--gold); font-size: 52px; line-height: 1; white-space: nowrap; }
  .offer-amount { font-weight: 700; font-size: 50px; line-height: 1; letter-spacing: -1px; white-space: nowrap; }
  .offer-amount .off { color: var(--gold); margin-left: 10px; }
  .offer-band { height: 27px; background: var(--gold); border-radius: 4px 0 0 4px; display: flex; align-items: center; padding-left: 11px; }
  .offer-band__title { font-family: "Montserrat", sans-serif; font-weight: 800; font-size: 23px; letter-spacing: 2px; color: var(--ink); white-space: nowrap; }
  .offer-band__note { margin-left: 10px; font-family: "Montserrat", sans-serif; font-weight: 500; font-size: 8.5px; line-height: 9px; letter-spacing: 1.2px; color: var(--white); white-space: nowrap; }

  .contact-title { font-family: "Montserrat", sans-serif; font-weight: 500; font-size: 15px; letter-spacing: 4px; color: var(--gold); display: flex; align-items: center; }
  .contact-title::after { content: ""; flex: 1; height: 1px; background: var(--gold); margin-left: 6px; }
  .contact-line { font-size: 12px; display: flex; align-items: center; gap: 6px; white-space: nowrap; }
  .contact-line svg { width: 11px; height: 11px; flex: none; }
  .contact-phone { font-family: "Montserrat", sans-serif; font-weight: 700; font-size: 12.5px; }
  .visit-box { height: 20px; border: 1px solid var(--gold); display: flex; align-items: center; white-space: nowrap; }
  .visit-box__label { font-family: "Montserrat", sans-serif; font-size: 7.5px; letter-spacing: 1px; color: var(--gold); padding: 0 8px; border-right: 1px solid var(--gold); line-height: 12px; white-space: nowrap; }
  .visit-box__url { font-family: "Montserrat", sans-serif; font-size: 11px; letter-spacing: 2px; padding-left: 8px; white-space: nowrap; }
  .visit-box__url b { font-weight: 800; }

  .front .contact-line, .front .visit-box__url { color: var(--ink); }

  /* BACK */
  .back-panel { left: 0; top: 0; width: 388px; height: 465px; background: radial-gradient(ellipse at 85% 10%, #2b2b2d 0%, var(--ink) 55%); }
  .back-heading { left: 29px; top: 30px; font-family: "Montserrat", sans-serif; font-weight: 800; font-size: 18px; letter-spacing: 1px; color: var(--gold); }
  .back-copy { left: 29px; top: 56px; width: 350px; font-size: 12.3px; line-height: 14.3px; color: var(--white); }
  .services-label { left: 27px; top: 252px; width: 28px; height: 94px; font-family: "Oswald", sans-serif; font-size: 15px; color: var(--white); writing-mode: vertical-rl; transform: rotate(180deg); text-align: center; }
  .service { display: flex; align-items: center; gap: 8px; }
  .service__hex { width: 33px; height: 37px; background: var(--white); clip-path: polygon(50% 0, 100% 25%, 100% 75%, 50% 100%, 0 75%, 0 25%); display: flex; align-items: center; justify-content: center; }
  .service__hex::before { content: ""; width: 27px; height: 31px; background: var(--gold); clip-path: polygon(50% 0, 100% 25%, 100% 75%, 50% 100%, 0 75%, 0 25%); }
  .service__name { font-weight: 600; font-size: 9px; line-height: 10.5px; color: var(--white); }
  .back .contact-line, .back .visit-box__url { color: var(--white); }

  .stamp-box { left: 605px; top: 19px; width: 64px; height: 75px; background: #b5b5b5; }
  .address-line { left: 433px; width: 235px; height: 1px; background: var(--ink); }
</style>
</head>
<body>

<section class="postcard postcard--front front" aria-label="Postcard front">
  <div class="abs front-hero"></div>
  <div class="abs storm-photo" role="img" aria-label="Photo of an orange house with a storm-damaged roof under dark clouds and lightning"></div>

  <div class="abs headline-top">POST STORM</div>
  <div class="abs headline-main">REPAIR</div>
  <div class="abs headline-script">Special</div>

  <div class="abs hex hex--intro">After the recent hurricanes its very important to have your roof checked</div>
  <div class="abs hex hex--detail-ring"></div>
  <div class="abs hex hex--detail">And any repairs fixed right away before they become a bigger more costly problem and that even though your home wasn't directly hit by the storm the high wind gust could've cause unseen damage.</div>

  <div class="abs brand-mark"></div>
  <div class="abs brand-name">CREST ROOFING</div>

  <div class="abs offer-script" style="left:330px; top:276px;">Offer</div>
  <div class="abs offer-amount" style="left:416px; top:270px; color:var(--ink);">$200<span class="off">OFF</span></div>
  <div class="abs offer-band" style="left:402px; top:325px; width:296px;">
    <span class="offer-band__title">ANY REPAIR</span>
    <span class="offer-band__note">*SOME RULES<br>MAY APPLY</span>
  </div>

  <div class="abs contact-title" style="left:363px; top:365px; width:335px;">CONTACT US</div>
  <div class="abs contact-line" style="left:363px; top:386px;">
    <svg viewBox="0 0 12 12" aria-hidden="true"><path d="M2.5 1 4.5 3 3.5 4.5C4.3 6.2 5.8 7.7 7.5 8.5L9 7.5 11 9.5 9.5 11C5 10.5 1.5 7 1 2.5Z" fill="var(--gold)"/></svg>
    <span class="contact-phone">877.512.DUNE</span>
  </div>
  <div class="abs contact-line" style="left:500px; top:386px;">
    <svg viewBox="0 0 12 12" aria-hidden="true"><rect x="1" y="3" width="10" height="7" fill="var(--gold)"/><path d="M1 3 6 7 11 3" stroke="var(--white)" fill="none"/></svg>
    <span>info@crestroofing.example</span>
  </div>
  <div class="abs visit-box" style="left:363px; top:413px; width:335px; border-radius:4px 0 0 4px; border-right:none;">
    <span class="visit-box__label">OR VISIT US AT</span>
    <span class="visit-box__url">www.<b>DuneRoofingco</b>.example</span>
  </div>
</section>

<section class="postcard postcard--back back" aria-label="Postcard back">
  <div class="abs back-panel"></div>

  <div class="abs back-heading">CREST ROOFING OFFERS</div>
  <p class="abs back-copy">an array of roofing solutions while providing professional, honest recommendations that address your specific needs. You can always count on us for exceptional service from the moment we meet. From inspection to installation, CREST has you covered.</p>

  <div class="abs offer-script" style="left:30px; top:156px;">Offer</div>
  <div class="abs offer-amount" style="left:118px; top:150px; color:var(--white);">$200<span class="off">OFF</span></div>
  <div class="abs offer-band" style="left:108px; top:207px; width:280px;">
    <span class="offer-band__title">ANY REPAIR</span>
    <span class="offer-band__note">*SOME RULES<br>MAY APPLY</span>
  </div>

  <div class="abs services-label">OTHER SERVICES</div>
  <div class="abs service" style="left:64px; top:256px;"><span class="service__hex"></span><span class="service__name">Retail/Commercial<br>Roof Replacement</span></div>
  <div class="abs service" style="left:230px; top:256px;"><span class="service__hex"></span><span class="service__name">Storm Damage Roof<br>Replacement</span></div>
  <div class="abs service" style="left:64px; top:304px;"><span class="service__hex"></span><span class="service__name">Repairs &amp; Restoration</span></div>
  <div class="abs service" style="left:230px; top:304px;"><span class="service__hex"></span><span class="service__name">New Construction</span></div>

  <div class="abs contact-title" style="left:20px; top:358px; width:356px;">CONTACT US</div>
  <div class="abs contact-line" style="left:20px; top:384px;">
    <svg viewBox="0 0 12 12" aria-hidden="true"><path d="M2.5 1 4.5 3 3.5 4.5C4.3 6.2 5.8 7.7 7.5 8.5L9 7.5 11 9.5 9.5 11C5 10.5 1.5 7 1 2.5Z" fill="var(--gold)"/></svg>
    <span class="contact-phone">877.512.DUNE</span>
  </div>
  <div class="abs contact-line" style="left:160px; top:384px;">
    <svg viewBox="0 0 12 12" aria-hidden="true"><rect x="1" y="3" width="10" height="7" fill="var(--gold)"/><path d="M1 3 6 7 11 3" stroke="var(--ink)" fill="none"/></svg>
    <span>info@crestroofing.example</span>
  </div>
  <div class="abs visit-box" style="left:20px; top:408px; width:346px; border-radius:4px;">
    <span class="visit-box__label" style="border-right:none;">OR VISIT US AT</span>
    <span class="visit-box__url">www.<b>DuneRoofingco</b>.example</span>
  </div>

  <div class="abs stamp-box"></div>
  <div class="abs address-line" style="top:189px;"></div>
  <div class="abs address-line" style="top:228px;"></div>
  <div class="abs address-line" style="top:263px;"></div>
  <div class="abs address-line" style="top:299px;"></div>
</section>

</body>
</html>
```